Social Media Templates for Fieldhouse Raffle Fund

We need a set of Square (1080 x 1080) social media posts.

My company works with sports clubs, helping them to raise money with a lottery.

I need a set of social media image that I can use to appeal to new Fieldhouse Raffle Fund to encourage them to start a lottery with us.

This landing page has worked very well for us https://fieldhouserafflefund.com/fieldhouse-raffle-fund/

THING THAT APPEAL TO CLUBS

No Setup Fees/Start for Free - (We don’t charge any registration fees, or setup fees so you can start raising money from the first draw.)

Start Straight Away - (A club can start raising money straight away.)

Sustainable Income - (The average player plays for 7 years)

Subscription Lottery - (once a player joins, they play until the choose to leave. A club doesn't have to sell tickets every draw to the same people)

All Administration Taken Care Of - (We do all the hard work, so they can focus on running their club.)

Unlimited Income - (There is no limit on the amount of money a club can raise: the more players, the more funds for the club.)

Fundraising reach - (Reach new fans)

50% of the sales is guaranteed profit

£25,000 jackpot - (a person could win £25,000 every week)

Price - (It costs just £1 per week to enter)

Help Your Club - (100% of the profit goes to the club who a player chooses to support)

You can see all the clubs we work with on www.fieldhouserafflefund.com

The images will also be used on Chatterwall. You can see some examples here https://www.chatterwall.com/FieldhouseRaffleFund/ (you may need a proxy to view this page as it is only viewable in the UK, so I have attached some screenshots)

You can find the Fieldhouse Raffle Fund Logo here https://www.logovault.com/winwellgroup/

Target Market(s)

People who are involved with amateur sports in United Kingdom

Industry/Entity Type

Gambling

Font styles to use
Sans Serif

Requirements
Must have
• My project must look great on social social media and encourage people to get in touch about starting a lottery with us.

Adobe Suite files must be provided

```html
<!DOCTYPE html>
<html lang="en">
<head>
<meta charset="utf-8">
<title>Fieldhouse Raffle Fund – Start Straight Away</title>
<link href="https://fonts.googleapis.com/css2?family=Raleway:wght@400;800&display=swap" rel="stylesheet">
<style>
  :root {
    --brand-blue: #2b80bb;
    --brand-orange: #ff6600;
    --paper: #ffffff;
    --photo-sky: #c9d6dc;
    --photo-kit: #2f6fd0;
    --photo-grass: #7fae3a;
  }
  html, body {
    margin: 0;
    padding: 0;
    width: 1200px;
    height: 1200px;
    overflow: hidden;
    background: var(--paper);
  }
  .post {
    position: relative;
    width: 1200px;
    height: 1200px;
    overflow: hidden;
    background: var(--paper);
    font-family: "Raleway", sans-serif;
  }
  .post__shapes {
    position: absolute;
    inset: 0;
  }
  .brand-name {
    position: absolute;
    left: 100px;
    top: 120px;
    width: 300px;
    margin: 0;
    color: var(--brand-blue);
    font-weight: 800;
    font-size: 46px;
    line-height: 1.12;
    text-transform: uppercase;
    letter-spacing: 0.5px;
  }
  .headline {
    position: absolute;
    left: 101px;
    top: 668px;
    margin: 0;
    color: var(--paper);
    font-weight: 800;
    font-size: 90px;
    line-height: 109px;
    letter-spacing: 0.5px;
    text-transform: uppercase;
  }
  .subline {
    position: absolute;
    left: 101px;
    top: 1008px;
    width: 620px;
    margin: 0;
    color: var(--paper);
    font-weight: 400;
    font-size: 49px;
    line-height: 59px;
  }
</style>
</head>
<body>
  <main class="post">
    <svg class="post__shapes" width="1200" height="1200" viewBox="0 0 1200 1200" aria-hidden="false">
      <defs>
        <linearGradient id="team-photo-tone" x1="0" y1="0" x2="0" y2="1">
          <stop offset="0" stop-color="var(--photo-sky)"/>
          <stop offset="0.25" stop-color="var(--photo-kit)"/>
          <stop offset="0.75" stop-color="var(--photo-kit)"/>
          <stop offset="1" stop-color="var(--photo-grass)"/>
        </linearGradient>
      </defs>
      <path class="band-orange" fill="var(--brand-orange)" d="M0,556 L640,210 L640,430 L0,686 Z"/>
      <path class="field-blue" fill="var(--brand-blue)" d="M0,686 C200,575 400,425 560,405 L1200,405 L1200,1200 L0,1200 Z"/>
      <path class="team-photo" role="img" aria-label="Photo of a youth football team in blue kits huddled together on a sunny pitch" fill="url(#team-photo-tone)"
        d="M749,0 L1200,0 L1200,770 L1040,856 Q996,880 952,858 L562,652 Q528,634 528,598 L528,372 Q528,340 554,318 Z"/>
    </svg>

    <p class="brand-name">Fieldhouse Raffle Fund</p>

    <h1 class="headline">Start<br>Straight<br>Away</h1>
    <p class="subline">A club can start raising money straight away.</p>
  </main>
</body>
</html>
```